Professional Photography Business cards

I need business cards that include my logo which I have uploaded. I run a photography business. I am open to ideas but I would like one side to have my logo and the other side to have my contact info. I don't have a website made but I do own a website domain. I have uploaded 2 different logo color schemes. My business colors are Blue, black , and white.

Business Name
Business Phone Number
Business Email
Business Website address
Instagram

Industry/Entity Type

Professional Photography

Contact Information for Business Card

Phone Number: 916-384-7702 email: info@tlane-studio.example Instagram: @t.lanestudio website doman- www.tlane-studio.example

Requirements
Must have
• I like the idea of a business card with a full black background front and back of card. My colors must include royal blue, black, and white

```html
<!DOCTYPE html>
<html lang="en">
<head>
<meta charset="utf-8">
<title>T. Lane Studio — Business Cards</title>
<link rel="stylesheet" href="https://fonts.googleapis.com/css2?family=Arimo:wght@400;700&display=swap">
<style>
  :root {
    --backdrop: #e4e4e4;
    --card-white: #f7f7f7;
    --royal-blue: #0a1aa8;
    --ink: #1a1a1a;
    --white: #ffffff;
  }
  * { box-sizing: border-box; margin: 0; padding: 0; }
  html, body {
    width: 1200px; height: 930px; overflow: hidden;
    background: var(--backdrop);
    font-family: "Arimo", Arial, sans-serif;
  }
  .canvas { position: relative; width: 1200px; height: 930px; }
  .card {
    position: absolute; width: 560px; height: 320px;
    box-shadow: 0 6px 18px rgba(0,0,0,0.12);
  }
  .card--contact { left: 50px; top: 450px; background: var(--card-white); color: var(--ink); }
  .card--brand { left: 590px; top: 160px; background: var(--royal-blue); color: var(--white); }

  .contact-list { position: absolute; left: 34px; top: 34px; list-style: none; }
  .contact-list li {
    display: flex; align-items: center; gap: 10px;
    font-size: 15px; line-height: 1; margin-bottom: 10px;
  }
  .contact-icon {
    width: 18px; height: 18px; border-radius: 50%;
    background: var(--royal-blue);
    display: flex; align-items: center; justify-content: center;
    flex: none;
  }

  .brand-mark { position: absolute; display: flex; align-items: center; gap: 14px; }
  .brand-mark__name { font-weight: 700; font-size: 34px; letter-spacing: 0.5px; }
  .brand-mark__dot { width: 54px; height: 54px; border-radius: 50%; border: 4px solid currentColor; flex: none; }
  .card--contact .brand-mark { left: 190px; top: 132px; }
  .card--contact .brand-mark__name { color: var(--royal-blue); }
  .card--contact .brand-mark__dot { color: var(--ink); }
  .card--brand .brand-mark { left: 50%; top: 50%; transform: translate(-50%, -50%); }

  .social-handle {
    position: absolute; right: 34px; bottom: 30px;
    display: flex; align-items: center; gap: 8px; font-size: 15px;
  }
  .social-handle__dot { width: 16px; height: 16px; border-radius: 50%; background: var(--royal-blue); }
</style>
</head>
<body>
<main class="canvas">
  <section class="card card--brand" aria-label="Card front">
    <div class="brand-mark">
      <span class="brand-mark__name">T. Lane Studio</span>
      <span class="brand-mark__dot"></span>
    </div>
  </section>

  <section class="card card--contact" aria-label="Card back">
    <ul class="contact-list">
      <li>
        <span class="contact-icon">
          <svg width="10" height="10" viewBox="0 0 10 10" aria-hidden="true"><path d="M2 1 L4 1 L4.6 3 L3.4 3.8 Q4.4 5.8 6.2 6.6 L7 5.4 L9 6 L9 8 Q8.6 9 7.6 9 Q1 8.4 1 2.4 Q1 1 2 1 Z" fill="#fff"/></svg>
        </span>
        916-384-7702
      </li>
      <li>
        <span class="contact-icon">
          <svg width="10" height="8" viewBox="0 0 10 8" aria-hidden="true"><rect x="0.5" y="0.5" width="9" height="7" fill="none" stroke="#fff"/><path d="M0.5 0.5 L5 4.5 L9.5 0.5" fill="none" stroke="#fff"/></svg>
        </span>
        info@tlane-studio.example
      </li>
      <li>
        <span class="contact-icon">
          <svg width="10" height="10" viewBox="0 0 10 10" aria-hidden="true"><circle cx="5" cy="5" r="4.3" fill="none" stroke="#fff"/><ellipse cx="5" cy="5" rx="1.8" ry="4.3" fill="none" stroke="#fff"/><line x1="0.7" y1="5" x2="9.3" y2="5" stroke="#fff"/></svg>
        </span>
        www.tlane-studio.example
      </li>
    </ul>

    <div class="brand-mark">
      <span class="brand-mark__name">T. Lane Studio</span>
      <span class="brand-mark__dot"></span>
    </div>

    <div class="social-handle">
      <span>@t.lanestudio</span>
      <span class="social-handle__dot"></span>
    </div>
  </section>
</main>
</body>
</html>
```